Silver Kite Venture Series Travel Brochure

I'm looking for a brochure design for a new travel product - Silver Kite Venture Series, catering for students above 12 years old. Target audience are schools that do destination projects. Brochure to be read by head teacher, parents and students.

Brochure should be A4 in size, 4-6 pages. Format of brochure is hard cover (a folder) with inlet for flyers. Flyers for destinations will be updated from time to time.

Finished job needs to be converted to electronic format for website and email proposal usage.

Attached is text to be used on brochure. Order of section can be adjusted.

For "Elements of the trip", please understand the contents and explain/display it in a graphic form.

For flyer, please come out with a template that I can use for other destinations. The main elements - what's included, number of days, location for pictures, itinerary, educational focus, should be alterable. Attached are text for two sample destinations.
Also attached (tour itinerary example) a version of flyer that I like.

I'm attaching some pictures here. If you find more suitable pictures, please feel free to use them.

Reason: I'm extending the deadline of this project by 4 days, as I need to add details & photo of another travel specialist in personnel session (total of 3 members). Also, in view of the amount of work a designer has to do for this project, I'm giving you more time for submission. Please do not hesitate to be in touch should you need more than 4 days extension. Thank you.

Target Market(s)

Schools - especially the head teacher and parents, to send students above 12 years old to travel

Industry/Entity Type

Electronic

Requirements
Must have
• This is a travel brochure with education elements in it. Parents feel better when their children are travelling for a purpose and lead by responsible teachers/adults whom they can trust. So, the design has to emphasis that education elements and safety are our utmost priority.
Nice to have
• We specialise in environmental study. So, it is nice to have the environmental touch in the design.
Should not have
• Our target market segment is the Middle East, which can be quite sensitive to religion. I prefer not to have any religious related illustration on the design.

```html
<!DOCTYPE html>
<html lang="en">
<head>
<meta charset="utf-8">
<title>Silver Kite Venture Series – What's included</title>
<link rel="stylesheet" href="https://fonts.googleapis.com/css2?family=Bevan&family=PT+Sans+Narrow:wght@400;700&family=Open+Sans:wght@400;600&display=swap">
<style>
  :root {
    --green: #5edc1c;
    --green-deep: #47c812;
    --green-light: #7cec34;
    --green-dark: #39b00c;
    --ink: #1a1a1a;
    --paper: #ffffff;
    --icon-dark: #262626;
    --hub-text: #eaffd8;
  }
  * { margin: 0; padding: 0; box-sizing: border-box; }
  html, body { width: 863px; height: 1200px; overflow: hidden; background: var(--paper); }
  .page { position: relative; width: 863px; height: 1200px; background: var(--paper); color: var(--ink); }
  .wheel-art { position: absolute; left: 0; top: 0; }
  .page-title {
    position: absolute; left: 65px; top: 103px;
    font-family: "Bevan", Georgia, serif; font-weight: 400; font-size: 22px; color: var(--green);
  }
  .element {
    position: absolute;
    font-family: "PT Sans Narrow", "Arial Narrow", sans-serif;
    font-size: 11.5px; line-height: 12.4px;
    hyphens: auto; -webkit-hyphens: auto;
  }
  .element h2 {
    font-family: "Bevan", Georgia, serif; font-weight: 400; font-size: 15px;
    line-height: 16px; color: var(--green);
  }
  .hub-label {
    position: absolute; left: 308px; top: 517px; width: 200px; text-align: center;
    font-family: "Bevan", Georgia, serif; font-size: 25px; line-height: 31px;
    color: var(--hub-text);
  }
  .closing {
    position: absolute; left: 65px; top: 1027px; width: 352px;
    font-family: "Open Sans", Arial, sans-serif; font-size: 14.5px; line-height: 19px;
    text-align: justify;
  }
  .closing .lead { font-variant: small-caps; font-weight: 600; font-size: 16px; }
</style>
</head>
<body>
<main class="page">
  <h1 class="page-title">What are the elements of the trips?</h1>

  <svg class="wheel-art" width="863" height="1200" viewBox="0 0 863 1200">
    <defs>
      <radialGradient id="hub-fill" cx="50%" cy="38%" r="62%">
        <stop offset="0%" stop-color="#96f44a"/>
        <stop offset="100%" stop-color="#55d818"/>
      </radialGradient>
      <filter id="soft-shadow" x="-10%" y="-10%" width="120%" height="120%">
        <feDropShadow dx="0" dy="3" stdDeviation="4" flood-color="#000" flood-opacity="0.25"/>
      </filter>
    </defs>
    <g class="spokes" stroke="var(--green)" stroke-width="1.4">
      <line x1="287" y1="250" x2="408" y2="578"/>
      <line x1="531" y1="250" x2="408" y2="578"/>
      <line x1="722" y1="410" x2="408" y2="578"/>
      <line x1="764" y1="652" x2="408" y2="578"/>
      <line x1="640" y1="865" x2="408" y2="578"/>
      <line x1="408" y1="948" x2="408" y2="578"/>
      <line x1="180" y1="865" x2="408" y2="578"/>
      <line x1="51" y1="652" x2="408" y2="578"/>
      <line x1="96" y1="409" x2="408" y2="578"/>
    </g>
    <g class="spokes-major" stroke="var(--green-deep)" stroke-width="2.4">
      <line x1="407" y1="320" x2="408" y2="578"/>
      <line x1="557" y1="383" x2="408" y2="578"/>
      <line x1="668" y1="550" x2="408" y2="578"/>
      <line x1="612" y1="733" x2="408" y2="578"/>
      <line x1="496" y1="857" x2="408" y2="578"/>
      <line x1="313" y1="857" x2="408" y2="578"/>
      <line x1="167" y1="735" x2="408" y2="578"/>
      <line x1="133" y1="549" x2="408" y2="578"/>
      <line x1="212" y1="392" x2="408" y2="578"/>
    </g>
    <g class="spoke-ends" fill="var(--green)">
      <circle cx="287" cy="250" r="4"/><circle cx="531" cy="250" r="4"/>
      <circle cx="722" cy="410" r="4"/><circle cx="764" cy="652" r="4"/>
      <circle cx="640" cy="865" r="4"/><circle cx="408" cy="948" r="4"/>
      <circle cx="180" cy="865" r="4"/><circle cx="51" cy="652" r="4"/>
      <circle cx="96" cy="409" r="4"/>
    </g>
    <g class="spoke-ends-major" fill="var(--green-deep)">
      <circle cx="407" cy="320" r="9"/><circle cx="557" cy="383" r="9"/>
      <circle cx="668" cy="550" r="9"/><circle cx="612" cy="733" r="9"/>
      <circle cx="496" cy="857" r="9"/><circle cx="313" cy="857" r="9"/>
      <circle cx="167" cy="735" r="9"/><circle cx="133" cy="549" r="9"/>
      <circle cx="212" cy="392" r="9"/>
    </g>
    <circle class="wheel" cx="408" cy="577" r="218" fill="var(--green-deep)" filter="url(#soft-shadow)"/>
    <circle class="hub-rim" cx="408" cy="577" r="120" fill="var(--green-dark)"/>
    <circle class="hub" cx="408" cy="577" r="112" fill="url(#hub-fill)"/>
    <g class="element-icons">
      <rect x="377" y="383" width="58" height="76" rx="6" fill="var(--green-light)" role="img" aria-label="Itinerary notebook icon"/>
      <rect x="478" y="425" width="76" height="72" rx="8" fill="var(--green-dark)" role="img" aria-label="Full time tour director with flag icon"/>
      <rect x="535" y="537" width="80" height="52" rx="5" fill="var(--green-light)" role="img" aria-label="Visa card icon"/>
      <rect x="512" y="632" width="84" height="74" rx="8" fill="var(--green-dark)" role="img" aria-label="Local guide with flag icon"/>
      <rect x="420" y="707" width="86" height="74" rx="8" fill="var(--green-dark)" role="img" aria-label="Local collaboration hands icon"/>
      <rect x="312" y="702" width="88" height="78" rx="8" fill="var(--green-dark)" role="img" aria-label="Food and drinks icon"/>
      <rect x="226" y="636" width="64" height="84" rx="8" fill="var(--green-dark)" role="img" aria-label="Travel insurance shield icon"/>
      <rect x="195" y="545" width="94" height="40" rx="3" fill="var(--icon-dark)" role="img" aria-label="Air ticket icon"/>
      <rect x="254" y="430" width="92" height="62" rx="6" fill="var(--green-dark)" role="img" aria-label="Accommodation bed icon"/>
    </g>
  </svg>

  <p class="hub-label">WHAT'S INCLUDED IN THE COST?</p>

  <section class="element element-tours" style="left:333px;top:178px;width:170px;">
    <h2>Tours</h2>
    <p>We will design an itinerary for the students to explore the essence of each destination. During the visits, we will incorporate educational element, be it environmental, geographical, historical or cultural. We will ensure stimulating experiences throughout the journey with suitable time for reflection and relaxation.</p>
  </section>

  <section class="element element-director" style="left:601px;top:240px;width:118px;">
    <h2>Full time<br>tour director</h2>
    <p>This person is your guide, friend and support throughout the tour. We will have at least one director on the trip, to travel with the group from the UAE and throughout the journey. Ratio is 1:8, 1 tour director or teacher to eight students.</p>
  </section>

  <section class="element element-accommodation" style="left:120px;top:300px;width:180px;">
    <h2>Accommodation</h2>
    <p>We organise suitable lodging for students at strategic location with best quality, where they can interact with their friends and meet local residents.</p>
  </section>

  <section class="element element-ticket" style="left:64px;top:512px;width:62px;">
    <h2>Air<br>ticket</h2>
    <p>We will arrange the best flight options available to you.</p>
  </section>

  <section class="element element-visa" style="left:697px;top:500px;width:60px;">
    <h2>Visa</h2>
    <p>We will assist with entry visas for all of the participants.</p>
  </section>

  <section class="element element-insurance" style="left:75px;top:731px;width:122px;">
    <h2>Travel<br>insurance</h2>
    <p>Travel insurance for each of the students is compulsory and can be arranged by Northgate Learning.</p>
  </section>

  <section class="element element-guide" style="left:651px;top:744px;width:100px;">
    <h2>Local tour<br>guide</h2>
    <p>We will have licensed local guides with extensive knowledge about each destination for specific location.</p>
  </section>

  <section class="element element-food" style="left:236px;top:873px;width:164px;">
    <h2>Food &amp; drinks</h2>
    <p>We will include all meals throughout the journey, ensuring quality and suitability at each of the destinations.</p>
  </section>

  <section class="element element-collaboration" style="left:497px;top:873px;width:124px;">
    <h2>Local<br>collaboration</h2>
    <p>We can arrange collaboration with local community, based on your requirements. For instance, school visit, charity fundraising, orphanage support, etc.</p>
  </section>

  <p class="closing"><span class="lead">Any situations that arise on the trips,</span> be it minor or major issues, will be handled professionally and promptly by our tour directors.</p>
</main>
</body>
</html>
```